MS word document templates for consultancy

I need the following templates for my business using my logo as branding.

- General report template
- Letter head template
- Tender proposal template

The templates should be sleek and with minimal colors, but with a small amount of green and grey where appropriate (as per attached logo and email signature). Font should be consistent with the text in the email signature.

```html
<!DOCTYPE html>
<html lang="en">
<head>
<meta charset="utf-8">
<title>Onward Talent – Letterhead</title>
<link rel="stylesheet" href="https://fonts.googleapis.com/css2?family=Montserrat:wght@400;500;600&family=Open+Sans:wght@400;600&display=swap">
<style>
  :root{
    --green:#3aa935;
    --grey:#8c8c8c;
    --ink:#3a3a3a;
    --paper:#ffffff;
    --soft:#e6e6e6;
  }
  *{box-sizing:border-box;margin:0;padding:0}
  html,body{width:755px;height:1200px;overflow:hidden;background:var(--paper)}
  .letterhead{position:relative;width:755px;height:1200px;background:var(--paper);
    font-family:"Open Sans",Arial,sans-serif;color:var(--ink)}
  .top-band{position:absolute;top:0;left:0;right:0;height:8px;background:var(--green)}
  .top-band::after{content:"";position:absolute;left:0;right:0;top:8px;height:3px;background:var(--soft)}
  .brand{position:absolute;left:58px;top:58px;font-family:"Montserrat",Arial,sans-serif;
    font-weight:500;font-size:32px;color:#444;letter-spacing:-0.3px}
  .subject{position:absolute;top:168px;left:0;right:0;text-align:center;
    font-family:"Montserrat",Arial,sans-serif;font-weight:500;font-size:14px;letter-spacing:2px;color:#555}
  .recipient{position:absolute;left:58px;top:222px;font-family:"Montserrat",Arial,sans-serif;line-height:1.45}
  .recipient .name{font-weight:600;font-size:15px;color:#333}
  .recipient .role{font-size:14px;color:#555}
  .recipient .phone{font-size:14px;color:var(--green);font-weight:500}
  .body{position:absolute;left:58px;right:58px;top:318px;font-size:11.5px;line-height:1.6;color:#555}
  .body p{margin-bottom:16px;text-align:justify}
  .signature{position:absolute;right:78px;top:800px;width:110px;height:44px;
    background:linear-gradient(90deg,#f2f2f2,#e4e4e4);border-radius:4px}
  .date{position:absolute;right:78px;top:852px;font-size:12px;color:#555}
  .footer{position:absolute;left:0;right:0;bottom:48px;text-align:center;font-size:11.5px;color:#555}
  .footer .row{display:flex;justify-content:center;gap:56px;margin-bottom:8px}
  .footer .item{display:inline-flex;align-items:center;gap:6px}
  .footer svg{width:11px;height:11px;fill:var(--green)}
  .bottom-band{position:absolute;left:0;right:0;bottom:0;height:34px;background:var(--green)}
  .bottom-band::before{content:"";position:absolute;left:0;right:0;top:-6px;height:3px;background:var(--soft)}
</style>
</head>
<body>
<main class="letterhead">
  <div class="top-band"></div>

  <div class="brand">Onward Talent</div>

  <h2 class="subject">SUBJECT</h2>

  <div class="recipient">
    <div class="name">Daniel Reyes</div>
    <div class="role">Managing Director</div>
    <div class="phone">P: 0400 123 456</div>
  </div>

  <section class="body">
    <p>Lorem ipsum dolor sit amet, consectetur adipiscing elit, sed do eiusmod tempor incididunt ut labore et dolore magna aliqua. Ut enim ad minim veniam, quis nostrud exercitation ullamco laboris nisi ut aliquip ex ea commodo consequat. Duis aute irure dolor in reprehenderit in voluptate velit esse cillum dolore eu fugiat nulla pariatur. Excepteur sint occaecat cupidatat non proident, sunt in culpa qui officia deserunt mollit anim id est laborum.</p>
    <p>Contrary to popular belief, Lorem Ipsum is not simply random text. It has roots in a piece of classical Latin literature from 45 BC, making it over 2000 years old.</p>
    <p>Sed ut perspiciatis unde omnis iste natus error sit voluptatem accusantium doloremque laudantium, totam rem aperiam, eaque ipsa quae ab illo inventore veritatis et quasi architecto beatae vitae dicta sunt explicabo. Nemo enim ipsam voluptatem quia voluptas sit aspernatur aut odit aut fugit.</p>
    <p>Contrary to popular belief, Lorem Ipsum is not simply random text. It has roots in a piece of classical Latin literature from 45 BC, making it over 2000 years old.</p>
  </section>

  <div class="signature" role="img" aria-label="Handwritten signature of the sender"></div>
  <div class="date">22/01/2023</div>

  <footer class="footer">
    <div class="row">
      <span class="item"><svg viewBox="0 0 12 12"><circle cx="6" cy="6" r="4"/></svg>info@onwardtalentgroup.com</span>
      <span class="item"><svg viewBox="0 0 12 12"><circle cx="6" cy="6" r="4"/></svg>www.onwardtalentgroup.com</span>
    </div>
    <div class="row">
      <span class="item"><svg viewBox="0 0 12 12"><path d="M6 0a4 4 0 0 0-4 4c0 3 4 8 4 8s4-5 4-8a4 4 0 0 0-4-4zm0 5.5A1.5 1.5 0 1 1 6 2.5a1.5 1.5 0 0 1 0 3z"/></svg>Dummy City, Dummy Country</span>
    </div>
  </footer>

  <div class="bottom-band"></div>
</main>
</body>
</html>
```